Photography business - business card design quick turn around

Create a business card design for me please. I actually need the final design back before the end of Sunday 13th May 7pm GMT. Sorry for the short notice.

Photoshop artwork template uploaded with artwork guidelines including printer profiles and other mandatory specifications. Only one side of the business card is required as the other side will be an image.

The design is required as an unflattened PSD file so that I can edit the text if I need to.

My brand colours are white and the teal you see in the logo. Occasionally I also use a dark grey on my website (I don't mind the shade of grey as appreciate grey on teal would be a different grey, to the grey I use on white on the website, so just use a shade of grey that matches). Font can be as the font for the logo or if you prefer I am open to another sans serif, easily legible font. Ideally font size will be 12+.Please do not use capital letters for text. I prefer everything to be lower case, if possible.

Thank you.

Lena

Target Market(s)

Other business owners who may refer me and families

Industry/Entity Type

Photographer

Contact Information for Business Card

Silver Kettle Photography Logo
Sub text: family portraiture, captured with love

Contact information, ideally using simple icons to represent email / website / facebook / instagram / pinterest

email: lena@silverkettlephotography.co.uk
website: silverkettlephotography.co.uk
facebook: @silverkettlephotography
pinterest: pinterest.com/silverkettlepho
instagram: @silverkettle_photography
mobile/telephone: 07713460291

If there is too much text then please drop the instagram and pinterest information.

Font styles to use
Sans Serif

Colors
33b8a4

Requirements
Must have
• Logo
• Contact details as listed above
• sub text
Nice to have
• Instagram and Pinterest contact details
• Nice to have icons to represent website / phone / facebook etc followered by the handle where relevant

```html
<!DOCTYPE html>
<html lang="en">
<head>
<meta charset="utf-8">
<title>Silver Kettle Photography – business card</title>
<link href="https://fonts.googleapis.com/css2?family=Didact+Gothic&family=Nunito+Sans:wght@700&display=swap" rel="stylesheet">
<style>
  :root {
    --teal: #33b8a4;
    --ink: #333333;
    --band: #4a4a4a;
    --card: #ffffff;
    --backdrop: #e6e7e8;
  }
  * { margin: 0; padding: 0; box-sizing: border-box; }
  html, body {
    width: 1200px; height: 1000px; overflow: hidden;
    background: var(--backdrop);
  }
  .business-card {
    position: absolute; left: 75px; top: 200px;
    width: 1050px; height: 600px;
    background: var(--card);
    border-radius: 34px;
    overflow: hidden;
    box-shadow: 0 10px 30px rgba(0,0,0,.18);
  }
  .brand {
    position: absolute; left: 90px; top: 190px; width: 330px;
  }
  .brand-name {
    display: flex; align-items: center; gap: 14px;
    font-family: "Didact Gothic", sans-serif;
    color: var(--teal);
    font-size: 34px; line-height: 1.1;
    text-transform: lowercase;
  }
  .brand-dot {
    flex: none; width: 22px; height: 22px; border-radius: 50%;
    background: var(--teal);
  }
  .brand-rule {
    margin-top: 14px; height: 2px; background: var(--ink);
  }
  .brand-tagline {
    margin-top: 6px;
    font-family: "Didact Gothic", sans-serif;
    font-size: 17px; color: var(--ink);
  }
  .divider {
    position: absolute; left: 455px; top: 90px;
    width: 2px; height: 300px; background: var(--ink);
  }
  .contacts {
    position: absolute; left: 490px; top: 108px;
    list-style: none;
    font-family: "Nunito Sans", sans-serif; font-weight: 700;
    font-size: 22px; color: var(--ink);
  }
  .contact {
    display: flex; align-items: center; gap: 10px;
    height: 42px;
  }
  .contact-icon {
    flex: none; width: 24px; height: 24px; border-radius: 50%;
    background: var(--teal);
    display: flex; align-items: center; justify-content: center;
  }
  .contact-icon svg { width: 14px; height: 14px; }
  .footer-band {
    position: absolute; left: 0; right: 0; top: 440px; height: 76px;
    background: var(--band);
    display: flex; align-items: center; justify-content: center;
    padding-left: 260px;
    font-family: "Didact Gothic", sans-serif;
    font-size: 32px; color: var(--teal);
  }
</style>
</head>
<body>
  <div class="business-card">
    <div class="brand">
      <div class="brand-name"><span class="brand-dot"></span><span>silver kettle photography</span></div>
      <div class="brand-rule"></div>
      <div class="brand-tagline">family portraiture, captured with love</div>
    </div>

    <div class="divider"></div>

    <ul class="contacts">
      <li class="contact">
        <span class="contact-icon"><svg viewBox="0 0 14 14"><path d="M3 1.5l2 2-1 1.5c.8 1.6 2 2.8 3.5 3.5l1.5-1 2 2-1.2 1.8C6 11 3 8 1.7 3.2z" fill="#fff"/></svg></span>
        07713460291
      </li>
      <li class="contact">
        <span class="contact-icon"><svg viewBox="0 0 14 14"><rect x="1.5" y="3.5" width="11" height="7" fill="none" stroke="#fff" stroke-width="1.4"/><path d="M1.5 3.5L7 8l5.5-4.5" fill="none" stroke="#fff" stroke-width="1.4"/></svg></span>
        lena@silverkettlephotography.co.uk
      </li>
      <li class="contact">
        <span class="contact-icon"><svg viewBox="0 0 14 14"><circle cx="7" cy="7" r="5.5" fill="none" stroke="#fff" stroke-width="1.3"/><ellipse cx="7" cy="7" rx="2.3" ry="5.5" fill="none" stroke="#fff" stroke-width="1.1"/><path d="M1.5 7h11" stroke="#fff" stroke-width="1.1"/></svg></span>
        silverkettlephotography.co.uk
      </li>
      <li class="contact">
        <span class="contact-icon"></span>
        @silverkettlephotography
      </li>
      <li class="contact">
        <span class="contact-icon"></span>
        silverkettlepho
      </li>
      <li class="contact">
        <span class="contact-icon"></span>
        @silverkettle_photography
      </li>
    </ul>

    <div class="footer-band">family portraiture, captured with love</div>
  </div>
</body>
</html>
```